NZ First of it's kind solutions directory and marketplace for busy Mums needs a business card design

We need a business card design for our new nationwide business in NZ (long term plans to go global). We provide solutions to the everyday challenges that busy Mums face by connecting them with quality communities and suppliers of carefully selected, relevant products and services. We sell direct via our online marketplace. The final design should communicate our values of inclusivity, quality and smart solutions. Colours should incorporate our logo colour palette of #477077 and #6ba8b2. Our website is at https://www.brightnestmums.example

Target Market(s)

busy Mums, Age 28 – 50, female, income over $100K, location main centres NZ primarily but NZ wide. Is likely juggling work or career with a young family. Probably had hobbies which have fallen by the wayside.
-Wants to succeed in her chosen career without compromising on family life
-to successfully juggle her career without feeling like she is compromising her children
- Is time poor, something always has to give and it’s generally her health (she’ll stay up late, get stressed)
- probably ex corporate or professional career. Has discretional income

Industry/Entity Type

Business

Contact Information for Business Card

Lena Forbisher, Founder, BrightNestMums.example (Strapline Tap; Gather; Sorted), 47 Kowhai Terrace, Ellerslie, Auckland 1051, New Zealand. Mob: 021 483 517 Ph: +64 (0)9 571 4860

Font styles to use
Other font styles liked:
• Raleway, and/or Architects Daughter

Colors
00a990
33b8a4
86cfc6
cfeae6

Requirements
Must have
• the above details, streamline. the logo and colours associated with those logos
Should not have
• foil or metallic colours

```html
<!DOCTYPE html>
<html lang="en">
<head>
<meta charset="utf-8">
<title>BrightNestMums – Business Card</title>
<link href="https://fonts.googleapis.com/css2?family=Raleway:ital,wght@0,500;0,700;1,500&family=Roboto+Condensed:wght@400&display=swap" rel="stylesheet">
<style>
  :root {
    --page: #ebebeb;
    --card: #fbfbfb;
    --teal-deep: #3e5f66;
    --teal: #5a9aa3;
    --ink: #2f3f44;
    --muted: #4a4f52;
  }
  * { box-sizing: border-box; margin: 0; padding: 0; }
  html, body { width: 1200px; height: 576px; overflow: hidden; }
  body { background: var(--page); position: relative; font-family: "Raleway", sans-serif; }

  .card {
    position: absolute;
    top: 138px;
    width: 484px;
    height: 294px;
    background: var(--card);
    border-radius: 14px;
    overflow: hidden;
  }
  .card--front { left: 82px; }
  .card--back { left: 602px; width: 480px; }

  .brand { position: absolute; display: flex; align-items: center; }
  .brand__dot { border-radius: 50%; background: var(--teal-deep); flex: none; }
  .brand__name { font-weight: 700; color: var(--teal-deep); letter-spacing: -0.3px; line-height: 1; }

  /* Front */
  .card--front .brand { left: 32px; top: 124px; }
  .card--front .brand__dot { width: 26px; height: 26px; margin-right: 12px; }
  .card--front .brand__name { font-size: 26px; }

  .strapline {
    position: absolute;
    left: 77px;
    top: 161px;
    font-size: 10px;
    font-weight: 500;
    letter-spacing: 4.4px;
    color: var(--muted);
    white-space: nowrap;
  }
  .strapline__sep { color: var(--teal); margin: 0 3px; }

  .decor-block {
    position: absolute;
    right: 0;
    top: 18px;
    width: 200px;
    height: 276px;
  }

  /* Back */
  .header-band {
    position: absolute;
    left: 0;
    top: 0;
    width: 100%;
    height: 92px;
    background: linear-gradient(90deg, var(--teal) 0%, var(--teal-deep) 60%);
  }
  .person { position: absolute; right: 26px; top: 26px; text-align: right; color: #fff; }
  .person__name { font-size: 21px; font-weight: 700; line-height: 1.1; }
  .person__role { font-size: 12px; font-style: italic; font-weight: 500; margin-top: 3px; }

  .card--back .brand { left: 28px; top: 108px; }
  .card--back .brand__dot { width: 38px; height: 38px; margin-right: 14px; }
  .card--back .brand__name { font-size: 33px; }

  .contacts {
    position: absolute;
    left: 32px;
    top: 190px;
    list-style: none;
    font-family: "Roboto Condensed", sans-serif;
    font-size: 12.5px;
    color: var(--ink);
  }
  .contacts__item { display: flex; align-items: center; height: 18.5px; }
  .contacts__icon { width: 11px; height: 11px; margin-right: 9px; fill: var(--teal-deep); flex: none; }

  .address {
    position: absolute;
    right: 32px;
    top: 228px;
    text-align: right;
    font-family: "Roboto Condensed", sans-serif;
    font-size: 12.5px;
    line-height: 18.5px;
    color: var(--ink);
    font-style: normal;
  }
</style>
</head>
<body>

<section class="card card--front">
  <div class="brand">
    <span class="brand__dot"></span>
    <span class="brand__name">BrightNestMums</span>
  </div>
  <p class="strapline">TAP<span class="strapline__sep">|</span>GATHER<span class="strapline__sep">|</span>SORTED</p>
  <svg class="decor-block" viewBox="0 0 200 276" role="img" aria-label="Large brand symbol decoration in deep teal">
    <defs>
      <linearGradient id="decorFill" x1="0" y1="0" x2="0" y2="1">
        <stop offset="0" stop-color="#5a9aa3"/>
        <stop offset="1" stop-color="#3e5f66"/>
      </linearGradient>
    </defs>
    <rect x="0" y="0" width="200" height="276" fill="url(#decorFill)"/>
  </svg>
</section>

<section class="card card--back">
  <div class="header-band" role="img" aria-label="Decorative teal header artwork"></div>

  <div class="person">
    <p class="person__name">Lena Forbisher</p>
    <p class="person__role">Founder</p>
  </div>

  <div class="brand">
    <span class="brand__dot"></span>
    <span class="brand__name">BrightNestMums</span>
  </div>

  <ul class="contacts">
    <li class="contacts__item">
      <svg class="contacts__icon" viewBox="0 0 12 12" aria-hidden="true"><path d="M3 0h6a1 1 0 0 1 1 1v10a1 1 0 0 1-1 1H3a1 1 0 0 1-1-1V1a1 1 0 0 1 1-1zm0.8 1.5v7.5h4.4V1.5zM6 9.7a0.8 0.8 0 1 0 0 1.6a0.8 0.8 0 1 0 0-1.6z"/></svg>
      021 483 517
    </li>
    <li class="contacts__item">
      <svg class="contacts__icon" viewBox="0 0 12 12" aria-hidden="true"><path d="M1 3.5C1 2 3 1 6 1s5 1 5 2.5V5H8.5V4h-5v1H1zM2.5 6h7l1.5 5H1z"/></svg>
      +64 (0)9 571 4860
    </li>
    <li class="contacts__item">
      <svg class="contacts__icon" viewBox="0 0 12 12" aria-hidden="true"><path d="M0 2h12v8H0zm1.2 1.2v0.4L6 7l4.8-3.4v-0.4z"/></svg>
      www.BrightNestMums.example
    </li>
    <li class="contacts__item">
      <svg class="contacts__icon" viewBox="0 0 12 12" aria-hidden="true"><circle cx="6" cy="6" r="5" fill="none" stroke="#3e5f66" stroke-width="1.2"/><path d="M1 6h10M6 1v10" stroke="#3e5f66" stroke-width="1"/></svg>
      lena@brightnestmums.example
    </li>
  </ul>

  <address class="address">
    47 Kowhai Terrace, Ellerslie,<br>
    Auckland 1051, New Zealand
  </address>
</section>

</body>
</html>
```